Visitenkarten und Briefpapier
Zielgruppe
Planung und Realisierung von individuellen und wertbeständigen Kamin- und Ofenlösungen, sowie Fliesen- und Baddesign.
Aufgabenstellung
Wir benötigen ein möglichst schlichtes Design für Visitenkarten, bzw. Briefpapier. Für die Visitenkarten gerne auch Vorschläge mit Prägung, Ausstanzung oder mit Heißfolie. Auch Klappkarten wären denkbar. Das Design soll "das gewisse Etwas haben" und nicht zu verspielt sein.
Die Visitenkarten sind für die Firma KORVA, das Logo von der Ausstellung "raumfunke" soll dezent mit eingebunden werden (bei dem Briefpapier z.B. in der Fußzeile". Die farbliche Gestaltung sollte sich an den Farben des Logos orientieren.
Schriftart für Texte: Century Gothic
Schriftfarbe: RAL 7016
Nur eine Idee: Ich könnte mir auch gut vorstellen, dass die Visitenkarte aus einer Zündholzverpackung (wenn dann aber eine besondere mit nur einem Zündholz oder einem besonders breiten) besteht: http://glimmvelo.de/produkte_briefchen.php

```html
<!DOCTYPE html>
<html lang="de">
<head>
<meta charset="utf-8">
<title>KORVA – Visitenkarte</title>
<link rel="stylesheet" href="https://fonts.googleapis.com/css2?family=Questrial&display=swap">
<style>
  :root {
    --anthracite: #1f292e;
    --anthracite-soft: #3a464c;
    --light: #e1e1e1;
    --orange: #c46e0e;
    --grey-text: #8c9296;
    --logo-light: #d6d6d6;
    --ink: #141a1d;
    --backdrop: #cfcfcf;
  }
  * { margin: 0; padding: 0; box-sizing: border-box; }
  html, body {
    width: 1200px; height: 840px; overflow: hidden;
    background: var(--backdrop);
    font-family: "Questrial", "Century Gothic", sans-serif;
  }
  .card {
    position: absolute; top: 252px;
    width: 520px; height: 336px;
    overflow: hidden;
    box-shadow: 0 6px 18px rgba(0,0,0,.25);
  }
  .card--front { left: 60px; background: var(--light); }
  .card--back {
    left: 620px;
    background: radial-gradient(circle at 40% 40%, #2e3a40, var(--anthracite) 70%);
  }
  .card__shape { position: absolute; inset: 0; }

  .brand { position: absolute; }
  .brand__name { display: block; letter-spacing: .05em; line-height: 1; }
  .brand__tagline { display: block; letter-spacing: .05em; }

  .card--front .brand { left: 28px; top: 28px; color: var(--ink); }
  .card--front .brand__name { font-size: 50px; }
  .card--front .brand__tagline { font-size: 14px; margin-top: 4px; }

  .address {
    position: absolute; left: 28px; top: 200px;
    color: var(--grey-text); font-size: 13px; line-height: 1.35;
    display: flex; gap: 8px;
  }
  .address svg { margin-top: 2px; flex: none; }

  .person { position: absolute; right: 30px; top: 100px; text-align: right; }
  .person__name { color: var(--orange); font-size: 22px; letter-spacing: .03em; }
  .person__role { color: var(--grey-text); font-size: 14px; margin-top: 2px; }

  .contact {
    position: absolute; right: 30px; bottom: 26px;
    list-style: none; color: var(--grey-text); font-size: 14px;
    text-align: right; letter-spacing: .03em;
  }
  .contact li { display: flex; justify-content: flex-end; align-items: center; gap: 10px; height: 24px; }
  .contact svg { flex: none; }

  .card--back .brand { left: 0; right: 0; top: 100px; text-align: center; color: var(--logo-light); }
  .card--back .brand__name { font-size: 92px; }
  .card--back .brand__tagline { font-size: 22px; margin-top: 6px; }
  .partner {
    position: absolute; right: 28px; bottom: 24px;
    color: var(--grey-text); font-size: 16px; letter-spacing: .04em;
  }
</style>
</head>
<body>

<section class="card card--front" aria-label="Vorderseite Visitenkarte">
  <svg class="card__shape" width="520" height="336" viewBox="0 0 520 336">
    <path d="M280 0 C215 60 185 170 212 336 L520 336 L520 0 Z" fill="var(--orange)"/>
    <path d="M290 0 C235 70 210 175 240 336 L520 336 L520 0 Z" fill="var(--anthracite-soft)"/>
    <path d="M300 0 C252 80 228 180 258 336 L520 336 L520 0 Z" fill="var(--orange)"/>
    <path d="M312 0 C270 90 252 190 288 336 L520 336 L520 0 Z" fill="var(--anthracite)"/>
  </svg>

  <div class="brand">
    <span class="brand__name">KORVA</span>
    <span class="brand__tagline">kamine · öfen · fliesen</span>
  </div>

  <div class="address">
    <svg width="12" height="16" viewBox="0 0 12 16"><path d="M6 0a6 6 0 0 0-6 6c0 4.5 6 10 6 10s6-5.5 6-10a6 6 0 0 0-6-6zm0 8.5A2.5 2.5 0 1 1 6 3.5a2.5 2.5 0 0 1 0 5z" fill="var(--anthracite)"/></svg>
    <div>Am Lindenhang 4c<br>34519 Wendhausen</div>
  </div>

  <div class="person">
    <div class="person__name">Jonas Berrit</div>
    <div class="person__role">Geschäftsführer</div>
  </div>

  <ul class="contact">
    <li>05637 / 41 82 70
      <svg width="16" height="16" viewBox="0 0 16 16"><path d="M3 1l3 3-2 2c1 2 3 4 6 6l2-2 3 3-2 2C7 15 1 9 1 3z" fill="none" stroke="var(--grey-text)" stroke-width="1.4"/></svg></li>
    <li>05637 / 41 82 78
      <svg width="16" height="16" viewBox="0 0 16 16"><rect x="4" y="1" width="8" height="4" fill="none" stroke="var(--grey-text)" stroke-width="1.3"/><rect x="1" y="5" width="14" height="7" fill="var(--grey-text)"/><rect x="4" y="10" width="8" height="5" fill="var(--anthracite)" stroke="var(--grey-text)" stroke-width="1.3"/></svg></li>
    <li>info@korva-wendhausen.de
      <svg width="16" height="12" viewBox="0 0 16 12"><rect x=".7" y=".7" width="14.6" height="10.6" fill="none" stroke="var(--grey-text)" stroke-width="1.3"/><path d="M1 1l7 6 7-6" fill="none" stroke="var(--grey-text)" stroke-width="1.3"/></svg></li>
  </ul>
</section>

<section class="card card--back" aria-label="Rückseite Visitenkarte">
  <div class="brand">
    <span class="brand__name">KORVA</span>
    <span class="brand__tagline">kamine · öfen · fliesen</span>
  </div>
  <div class="partner">raumfunke</div>
</section>

</body>
</html>
```